Logo + Label Design (Men’s Grooming Brand & Product Packaging)

Design a logo and 2 oz pomade label for Brel, a modern men’s grooming brand focused on clean, high-quality, natural ingredients. The design should establish a bold, masculine, minimalist identity that can later extend to products like shaving gel and body wash.

Key Requirements

Create a primary logo for “Brel” and a core label for the 2 oz pomade jar (screw-top).

Use a clean, modern style — masculine, confident, and approachable (think Dorran’s, Velta, Northfield Kit).

Design for 1–2 color screen printing on solid jar colors (white, black, or navy).

Avoid gradients, foil, or embossing. Must work in black & white.

Provide: vector logo, mockup of the 2 oz jar, color palette (CMYK/RGB/HEX), and font specs.

Winning design may lead to future projects (body wash, shave gel, skincare lines).

Font styles to use
Other font styles liked:
• We like the fonts and design concept in the attached mockup.

Requirements
Should not have
• We want to avoid too much writing or busy designs. We want to avoid having graphics/illustrations embedded in the logo if they will cause the brand to look less classy or sophisticated. We also want the design to look simple and all-American (e.g. Hollister and Vane, Pine Ledger, The KIM, etc). We’d like to give a Pellham & Royce vibe that feels classy and high end.

```html
<!DOCTYPE html>
<html lang="en">
<head>
<meta charset="utf-8">
<title>Brel — Crisp &amp; Pure Hair Pomade Label</title>
<link rel="stylesheet" href="https://fonts.googleapis.com/css2?family=DM+Serif+Display&display=swap">
<style>
  :root {
    --ink: #0b0b0b;
    --paper: #ffffff;
    --label-text: #ffffff;
  }
  * { margin: 0; padding: 0; box-sizing: border-box; }
  html, body {
    width: 1200px;
    height: 1200px;
    overflow: hidden;
    background: var(--paper);
  }
  .canvas {
    width: 1200px;
    height: 1200px;
    display: flex;
    align-items: center;
    justify-content: center;
  }
  .label {
    width: 600px;
    height: 1000px;
    background: var(--ink);
    color: var(--label-text);
    font-family: "DM Serif Display", serif;
    font-weight: 400;
    display: flex;
    flex-direction: column;
    align-items: center;
    padding: 120px 60px 90px;
  }
  .brand-name {
    font-size: 230px;
    font-weight: 400;
    line-height: 0.9;
    letter-spacing: -4px;
    text-transform: lowercase;
  }
  .product-line {
    margin-top: 50px;
    font-size: 62px;
    line-height: 1;
    white-space: nowrap;
  }
  .product-type {
    margin-top: 70px;
    font-size: 62px;
    line-height: 1;
    white-space: nowrap;
  }
  .product-details {
    margin-top: auto;
    text-align: center;
    font-size: 27px;
    line-height: 1.45;
    white-space: nowrap;
  }
</style>
</head>
<body>
  <main class="canvas">
    <section class="label">
      <h1 class="brand-name">brel</h1>
      <p class="product-line">Crisp &amp; Pure</p>
      <p class="product-type">Hair Pomade</p>
      <div class="product-details">
        <p>Medium Hold - Matte Finish</p>
        <p>Net WT 2 oz (57g)</p>
      </div>
    </section>
  </main>
</body>
</html>
```